Mastering Modern Vineyard Management

size of the ad - 8”x 10.75" plus 0.25" bleed
I would like an ad for a magazine that will stand out and make people want to read the ad.
The ad should not be crowded and people reading the ad will be able to read the text.
I would like it to be a creative and modern-day design.
the list of topics should not be the focus of the ad.
the text is attached.
If you decide to use people in the ad then please no ladies.
please note that leave over 1 inch for the bottom of the footer

```html
<!DOCTYPE html>
<html lang="en">
<head>
<meta charset="utf-8">
<title>Course Magazine Ad</title>
<link href="https://fonts.googleapis.com/css2?family=Bebas+Neue&family=Poppins:wght@400;500;600;700;800&display=swap" rel="stylesheet">
<style>
  :root {
    --red: #e30b1f;
    --navy: #0b1565;
    --ink: #2b2b33;
    --grey: #3a3a40;
    --white: #ffffff;
    --canvas: #ffffff;
  }
  * { margin: 0; padding: 0; box-sizing: border-box; }
  html, body { width: 1200px; height: 2785px; overflow: hidden; background: var(--canvas); }
  .ad-page {
    position: absolute; left: 50px; top: 659px;
    width: 1100px; height: 1467px;
    background: var(--white);
    box-shadow: 0 12px 40px rgba(0,0,0,0.28);
    overflow: hidden;
    font-family: "Poppins", sans-serif;
  }
  .ad-page > * { position: absolute; }
  .headline {
    left: 72px; top: 58px;
    font-family: "Bebas Neue", sans-serif;
    font-size: 150px; line-height: 1; color: var(--red);
    letter-spacing: 1px; white-space: nowrap;
  }
  .subheadline {
    left: 76px; top: 193px;
    font-weight: 700; font-size: 40px; line-height: 1; color: var(--navy);
    white-space: nowrap; letter-spacing: -0.3px;
  }
  .hero-photo {
    left: 0; top: 239px; width: 1100px; height: 438px;
    background: linear-gradient(180deg, #ffffff 0%, #e9edf0 25%, #c9d0d0 48%, #8e9d93 70%, #6f8571 100%);
  }
  .slogan-band {
    left: 0; top: 677px; width: 1100px; height: 181px;
    background: var(--navy); color: var(--white);
    padding: 18px 0 0 74px;
    font-weight: 500; font-size: 63px; line-height: 70px; letter-spacing: -0.5px;
    white-space: nowrap;
  }
  .location {
    left: 72px; top: 880px;
    font-weight: 800; font-size: 82px; line-height: 1; color: var(--red);
  }
  .schedule { left: 74px; top: 965px; font-weight: 600; font-size: 43px; line-height: 42px; text-transform: uppercase; }
  .schedule .count { color: var(--navy); display: block; }
  .schedule .evenings { color: var(--grey); display: block; }
  .start-date {
    left: 74px; top: 1060px; width: 464px; height: 66px;
    border: 3px solid var(--red); border-radius: 12px; overflow: hidden;
    display: flex;
  }
  .start-date .label {
    width: 177px; display: flex; align-items: center; justify-content: center;
    font-weight: 600; font-size: 31px; color: var(--grey);
  }
  .start-date .date {
    flex: 1; background: var(--navy); color: var(--white);
    font-family: "Bebas Neue", sans-serif; font-size: 58px; line-height: 64px;
    padding-left: 14px;
  }
  .start-date .date sup { font-size: 28px; vertical-align: 22px; line-height: 0; }
  .scholarships {
    left: 74px; top: 1134px;
    font-weight: 700; font-size: 26.5px; color: var(--grey); white-space: nowrap;
  }
  .early-bird {
    left: 76px; top: 1173px; width: 466px; height: 145px;
    border: 3px solid var(--red); border-radius: 16px; overflow: hidden;
  }
  .early-bird .title {
    background: var(--red); color: var(--white);
    height: 64px; padding-left: 16px;
    font-weight: 700; font-size: 40px; line-height: 66px; white-space: nowrap;
  }
  .early-bird .note {
    padding: 8px 0 0 19px;
    font-weight: 500; font-size: 26px; line-height: 32px; color: var(--ink);
  }
  .topics { left: 604px; top: 884px; }
  .topics h2 { font-weight: 700; font-size: 33px; line-height: 1; color: var(--navy); margin-bottom: 12px; }
  .topics ul { list-style: none; }
  .topics li {
    display: flex; align-items: center; height: 41px;
    font-weight: 400; font-size: 21px; color: var(--ink);
  }
  .topics li svg { width: 16px; height: 16px; margin: 0 14px 0 6px; flex: none; }
</style>
</head>
<body>
  <main class="ad-page">
    <h1 class="headline">VITICULTURE COURSE</h1>
    <p class="subheadline">MASTERING MODERN VINEYARD MANAGEMENT</p>
    <div class="hero-photo" role="img" aria-label="Photo of an open hand held out above a hazy aerial landscape view"></div>
    <p class="slogan-band">INVESTING IN KNOWLEDGE IS<br>INVESTING IN OPPORTUNITIES.</p>

    <p class="location">LARKFIELD</p>
    <p class="schedule"><span class="count">10 -Tuesday</span><span class="evenings">Evenings Sessions</span></p>
    <div class="start-date">
      <span class="label">STARTING</span>
      <span class="date">28<sup>TH</sup> FEBRUARY</span>
    </div>
    <p class="scholarships">LIMITED PARTIAL SCHOLARSHIPS</p>
    <div class="early-bird">
      <p class="title">EARLY BIRD SPECIAL</p>
      <p class="note">For those that started or would<br>like to go into grape growing</p>
    </div>

    <section class="topics">
      <h2>TOPICS: PARTIAL LISTING</h2>
      <ul>
        <li><svg viewBox="0 0 16 16"><circle cx="8" cy="8" r="6.8" fill="none" stroke="#0b1565" stroke-width="1.4"/><path d="M5 8.2l2 2 4-4" fill="none" stroke="#0b1565" stroke-width="1.4"/></svg>Vineyard investment strategies</li>
        <li><svg viewBox="0 0 16 16"><circle cx="8" cy="8" r="6.8" fill="none" stroke="#0b1565" stroke-width="1.4"/><path d="M5 8.2l2 2 4-4" fill="none" stroke="#0b1565" stroke-width="1.4"/></svg>Site selection</li>
        <li><svg viewBox="0 0 16 16"><circle cx="8" cy="8" r="6.8" fill="none" stroke="#0b1565" stroke-width="1.4"/><path d="M5 8.2l2 2 4-4" fill="none" stroke="#0b1565" stroke-width="1.4"/></svg>Financing</li>
        <li><svg viewBox="0 0 16 16"><circle cx="8" cy="8" r="6.8" fill="none" stroke="#0b1565" stroke-width="1.4"/><path d="M5 8.2l2 2 4-4" fill="none" stroke="#0b1565" stroke-width="1.4"/></svg>Soil and irrigation</li>
        <li><svg viewBox="0 0 16 16"><circle cx="8" cy="8" r="6.8" fill="none" stroke="#0b1565" stroke-width="1.4"/><path d="M5 8.2l2 2 4-4" fill="none" stroke="#0b1565" stroke-width="1.4"/></svg>Canopy management</li>
        <li><svg viewBox="0 0 16 16"><circle cx="8" cy="8" r="6.8" fill="none" stroke="#0b1565" stroke-width="1.4"/><path d="M5 8.2l2 2 4-4" fill="none" stroke="#0b1565" stroke-width="1.4"/></svg>Vineyard Legal basics</li>
        <li><svg viewBox="0 0 16 16"><circle cx="8" cy="8" r="6.8" fill="none" stroke="#0b1565" stroke-width="1.4"/><path d="M5 8.2l2 2 4-4" fill="none" stroke="#0b1565" stroke-width="1.4"/></svg>Pest control</li>
        <li><svg viewBox="0 0 16 16"><circle cx="8" cy="8" r="6.8" fill="none" stroke="#0b1565" stroke-width="1.4"/><path d="M5 8.2l2 2 4-4" fill="none" stroke="#0b1565" stroke-width="1.4"/></svg>Harvest planning</li>
        <li><svg viewBox="0 0 16 16"><circle cx="8" cy="8" r="6.8" fill="none" stroke="#0b1565" stroke-width="1.4"/><path d="M5 8.2l2 2 4-4" fill="none" stroke="#0b1565" stroke-width="1.4"/></svg>Dealing with wineries</li>
        <li><svg viewBox="0 0 16 16"><circle cx="8" cy="8" r="6.8" fill="none" stroke="#0b1565" stroke-width="1.4"/><path d="M5 8.2l2 2 4-4" fill="none" stroke="#0b1565" stroke-width="1.4"/></svg>Tax fundamentals</li>
      </ul>
    </section>
  </main>
</body>
</html>
```